Quick Straightforward Billboard Redesign

- Design billboard sized for 10 foot' x 36' foot width live area size and please include bleeds 6" around all sides
- Exact blue color match is imperative in headline, logo, phone number bubble or wherever used. C-83 / M-45 / Y-1 / K-0-
- What I hope to illustrate is that our company offers the best porch screening in the area area, in regards to quality, expertise, durability, storms proof, but we do not build screen porches.
- Current board is attached below from previous designer, and as you can see sizing was off, white space on edges make it appear to be sized incorrectly.
- I also attached my own little mock up idea well well if it helps, favorite image, logo, headline, etc and ideas perhaps on expanding or making this better?

Thanks so much!

Target Market(s)

Drivers and passengers, Southeastern NC, are of immense new construction and high end homes.

Industry/Entity Type

Construction

Colors
0054AA
0677BA
7BADD7
CADEEF
E8F1F8

Requirements
Must have
• Blue color matching
Nice to have
• Design spins or other thoughts on my little mock up

```html
<!DOCTYPE html>
<html lang="en">
<head>
<meta charset="utf-8">
<title>Porch Screening Billboard</title>
<link href="https://fonts.googleapis.com/css2?family=Anton&family=Oswald:wght@500;700&display=swap" rel="stylesheet">
<style>
  :root {
    --brand-blue: #0064B4;
    --brand-blue-deep: #0054AA;
    --coast-green: #0DB04B;
    --panel-white: #FFFFFF;
    --page-bg: #E8F1F8;
    --photo-sky: #7BADD7;
    --photo-stone: #D9D6CE;
    --photo-lawn: #8DB45A;
  }
  * { margin: 0; padding: 0; box-sizing: border-box; }
  html, body {
    width: 1200px;
    height: 1200px;
    overflow: hidden;
    background: var(--page-bg);
  }
  .canvas {
    width: 1200px;
    height: 1200px;
    display: flex;
    align-items: center;
    justify-content: center;
  }
  .billboard {
    width: 1120px;
    height: 374px;
    display: flex;
    background: var(--panel-white);
    box-shadow: 0 10px 30px rgba(0, 40, 90, 0.18);
    overflow: hidden;
  }
  .message-panel {
    flex: none;
    width: 480px;
    padding: 34px 24px 26px 32px;
    display: flex;
    flex-direction: column;
    align-items: flex-start;
    justify-content: center;
  }
  .headline {
    font-family: "Anton", "Oswald", sans-serif;
    font-weight: 400;
    line-height: 1.04;
    letter-spacing: 0.3px;
    white-space: nowrap;
  }
  .headline-top {
    display: block;
    font-size: 52px;
    color: var(--brand-blue);
  }
  .headline-bottom {
    display: block;
    font-size: 52px;
    color: var(--coast-green);
  }
  .company-name {
    margin-top: 18px;
    margin-left: 22px;
    display: flex;
    align-items: center;
    gap: 10px;
    font-family: "Oswald", sans-serif;
    font-weight: 500;
    font-size: 32px;
    line-height: 1.1;
    letter-spacing: 0.3px;
    color: var(--brand-blue);
    text-transform: uppercase;
    white-space: nowrap;
  }
  .company-mark {
    flex: none;
    width: 26px;
    height: 26px;
    background: var(--brand-blue);
  }
  .phone-pill {
    margin-top: 10px;
    margin-left: 16px;
    display: flex;
    align-items: center;
    gap: 12px;
    padding: 4px 24px 6px 18px;
    background: var(--brand-blue);
    border-radius: 18px;
    color: var(--panel-white);
    font-family: "Oswald", sans-serif;
    font-weight: 700;
    font-size: 52px;
    line-height: 1.1;
    letter-spacing: 1px;
    white-space: nowrap;
  }
  .phone-icon { width: 32px; height: 38px; flex: none; }
  .porch-photo {
    flex: 1;
    background:
      linear-gradient(180deg,
        #F4F6F8 0%, #EEF1F4 18%,
        var(--photo-sky) 26%, #A9CBE6 36%,
        #5E8F4E 40%, var(--photo-lawn) 50%,
        var(--photo-stone) 60%, #C9C4B9 100%);
  }
</style>
</head>
<body>
  <main class="canvas">
    <section class="billboard">
      <div class="message-panel">
        <h1 class="headline">
          <span class="headline-top">Screen Your Porch</span>
          <span class="headline-bottom">Built for the Coast</span>
        </h1>
        <div class="company-name">
          <span class="company-mark"></span>
          <span>Tidemark Screenworks</span>
        </div>
        <div class="phone-pill">
          <svg class="phone-icon" viewBox="0 0 34 40" aria-hidden="true">
            <path d="M8 3 L13 3 L15 12 L11 15 C12 21 15 26 19 29 L23 26 L30 30 L29 36 C27 38 23 38 19 36 C11 31 5 22 4 12 C4 8 5 5 8 3 Z" fill="#FFFFFF"/>
            <path d="M21 10 A8 8 0 0 1 27 17" stroke="#FFFFFF" stroke-width="2.4" fill="none" stroke-linecap="round"/>
            <path d="M22 4 A14 14 0 0 1 32 16" stroke="#FFFFFF" stroke-width="2.4" fill="none" stroke-linecap="round"/>
          </svg>
          <span>910.555.0148</span>
        </div>
      </div>
      <div class="porch-photo" role="img" aria-label="Photo of a bright screened porch with white ceiling and fan, wicker lounge chairs on stone pavers, a potted palm, and a view of lawn and lake beyond"></div>
    </section>
  </main>
</body>
</html>
```